New web design for a service provider in the medical field

We are looking for a new design for our website. We are a company that repairs and sells medical endoscopes. Our customers include doctors and hospitals. Our current website can be found at https://lumavex.de/en/lumavex-english.
We need a new web design (without programming) for the following 3 pages:
-Startpage https://lumavex.de/en/lumavex-english/
-Used endoscopes https://lumavex.de/en/used-endoscopes/
-Purchase https://lumavex.de/en/purchase/
The design should be modern and stylish.
The blue color of the logo should be reflected on the page, but not too intrusive.
I have uploaded the images from the header. If more images are needed, let me know and I will upload them.

Target Market(s)
Doctors and hospitals

```html
<!DOCTYPE html>
<html lang="en">
<head>
<meta charset="utf-8">
<title>Lumavex – Endoscope Repair</title>
<link rel="stylesheet" href="https://fonts.googleapis.com/css2?family=Red+Hat+Display:wght@400;500;700;800;900&display=swap">
<style>
:root{
  --blue:#2a9fe0;
  --blue-bright:#35a9ee;
  --navy:#123a5c;
  --navy-deep:#0d2c47;
  --ink:#17304a;
  --text:#3b4a59;
  --pale:#eaf4fb;
  --line:#d5e6f3;
  --white:#fff;
  --red:#e0281f;
}
*{box-sizing:border-box;margin:0;padding:0}
html,body{width:1200px;height:4866px;overflow:hidden}
body{position:relative;font-family:"Red Hat Display",Arial,sans-serif;color:var(--text);background:var(--white)}
.abs{position:absolute}
.btn{position:absolute;display:flex;align-items:center;justify-content:center;border-radius:24px;font-weight:700;font-size:12px;letter-spacing:.4px;text-transform:uppercase;color:#fff}
.btn-blue{background:var(--blue)}
.btn-navy{background:var(--navy)}
.wordmark{font-weight:700;color:var(--navy);letter-spacing:.2px}
/* header */
.topbar{left:680px;top:0;width:520px;height:32px;background:var(--blue);border-bottom-left-radius:18px;display:flex;align-items:center;gap:26px;padding-left:30px;color:#fff;font-size:12px;font-weight:700}
.topbar span{display:flex;align-items:center;gap:7px}
.logo{left:100px;top:24px;display:flex;align-items:center;gap:10px}
.logo .dot{width:16px;height:16px;border-radius:50%;background:var(--blue)}
.logo .wordmark{font-size:24px}
.logo small{display:block;font-size:10px;color:var(--blue);font-weight:500}
.nav{left:305px;top:62px;display:flex;gap:29px;font-size:12px;font-weight:700;color:var(--ink)}
.nav .active{border-bottom:2px solid var(--blue);padding-bottom:5px}
/* hero */
.hero{left:0;top:100px;width:1200px;height:600px;background:linear-gradient(120deg,#0e3e66 0%,#1f6fa8 45%,#3aa4de 100%)}
.hero-photo{left:540px;top:100px;width:660px;height:560px;background:linear-gradient(200deg,rgba(255,255,255,.35),rgba(255,255,255,.05) 70%)}
.hero-text{left:105px;top:272px;color:#fff}
.hero-text p{font-size:26px;font-weight:500}
.hero-text h1{font-size:37px;font-weight:900;line-height:1.15;margin-top:6px}
/* service */
.service{left:135px;top:790px;width:935px;height:270px;background:var(--navy);border-radius:40px 40px 0 40px;color:#fff;text-align:center;padding-top:50px}
.service h2{font-size:36px;font-weight:900}
.service h2 span{color:var(--blue-bright)}
.service p{font-size:19px;line-height:1.45;margin:38px auto 0;width:740px;color:#dbe8f3}
/* intro */
.intro-photo{left:0;top:1180px;width:550px;height:460px;border-radius:0 230px 230px 0;background:radial-gradient(circle at 55% 45%,#6b7580,#c9d0d6 60%,#eef1f4);border:3px solid var(--blue)}
.intro{left:587px;top:1225px;width:520px}
.intro h3{font-size:26px;font-weight:700;color:var(--ink);line-height:1.35}
.intro p{font-size:13.5px;line-height:1.75;margin-top:16px;padding-left:5px}
.brands{left:592px;top:1548px;display:flex;gap:15px}
.brands div{width:150px;height:46px;display:flex;align-items:center;justify-content:center;color:#fff;font-weight:900;font-size:18px;letter-spacing:.5px}
/* cards */
.card{position:absolute;top:1765px;width:315px;height:285px;border:2px solid var(--blue);border-radius:40px 0 40px 40px;padding:60px 38px 0}
.card h4{font-size:22px;font-weight:700;color:var(--ink);text-transform:uppercase}
.card h5{font-size:16px;font-weight:500;margin-top:2px}
.card p{font-size:11.5px;line-height:1.6;margin-top:10px}
.card .icon{position:absolute;top:-38px;left:38px;width:76px;height:76px;border-radius:50%;background:var(--blue);border:4px solid #fff;display:flex;align-items:center;justify-content:center}
.card.featured{background:var(--blue);border:none;color:#fff}
.card.featured h4,.card.featured h5{color:#fff}
.card.featured .icon{background:var(--navy)}
/* faulty */
.faulty{left:0;top:2130px;width:1200px;height:550px;background:linear-gradient(90deg,#f4f8fb,#dbeaf5)}
.faulty-text{left:130px;top:2235px;width:420px}
.faulty-text h2{font-size:38px;font-weight:700;color:var(--ink)}
.faulty-text h2 span{color:var(--blue)}
.faulty-text h3{font-size:23px;font-weight:500;color:var(--ink);margin-top:24px}
.faulty-text p{font-size:15px;line-height:1.65;margin-top:18px}
.faulty-photo{left:618px;top:2168px;width:480px;height:480px;border-radius:50%;border:8px solid var(--blue);background:radial-gradient(circle at 50% 45%,#40464c,#a9b1b8 55%,#eef1f4)}
/* outcome */
.h-center{position:absolute;left:0;width:1200px;text-align:center;font-weight:800;color:var(--ink)}
.grid{left:125px;top:2820px;width:950px;height:505px;display:grid;grid-template-columns:repeat(3,1fr);grid-template-rows:243px 262px}
.cell{padding:100px 40px 0 38px;border-right:1px solid var(--line);border-bottom:1px solid var(--line);position:relative}
.cell:nth-child(3n){border-right:none}
.cell:nth-child(n+4){border-bottom:none}
.cell h4{font-size:18px;font-weight:700;color:var(--ink);line-height:1.15}
.cell p{font-size:13px;line-height:1.5;margin-top:10px}
.cell .ico{position:absolute;left:42px;top:38px}
.cell.hl{background:linear-gradient(135deg,#1d7fc4,#3ab0ee);color:#fff;padding-left:40px}
.cell.hl h4{color:#fff}
/* decision */
.decision{left:0;top:3390px;width:1200px;height:560px;background:var(--pale)}
.feat{position:absolute;width:250px;font-size:9.5px;line-height:1.45}
.feat h5{font-size:14px;font-weight:700;color:var(--ink);margin-bottom:3px}
.feat.l{text-align:right}
.fi{position:absolute;width:56px;height:56px;border-radius:50%;display:flex;align-items:center;justify-content:center}
.fi.b{background:var(--blue)}
.fi.n{background:var(--navy-deep)}
/* help */
.help{left:0;top:3950px;width:1200px;height:570px;background:linear-gradient(180deg,var(--navy-deep),#143f63)}
.field{position:absolute;height:42px;border:1px solid #46698a;display:flex;align-items:center;gap:10px;padding-left:18px;font-size:12px;font-weight:700;color:#fff}
/* footer */
.footer{left:0;top:4520px;width:1200px;height:346px;background:var(--blue);color:#fff}
.fcol{position:absolute;top:4583px;font-size:13px;line-height:29px}
.fcol h6{font-size:13px;font-weight:800;letter-spacing:.4px;margin-bottom:8px}
</style>
</head>
<body>

<!-- header -->
<div class="abs topbar">
  <span><svg width="16" height="16" viewBox="0 0 16 16"><circle cx="8" cy="8" r="8" fill="#fff"/><rect x="4" y="5" width="8" height="6" fill="none" stroke="#2a9fe0"/><path d="M4 5l4 3 4-3" fill="none" stroke="#2a9fe0"/></svg>info@lumavex.de</span>
  <span><svg width="16" height="16" viewBox="0 0 16 16"><circle cx="8" cy="8" r="8" fill="#fff"/><path d="M5 4l2 0 1 2-1 1c1 1 1 2 2 2l1-1 2 1v2c-4 0-7-3-7-7z" fill="#2a9fe0"/></svg>+49 4151 555 012-0</span>
  <span>ENG ⌄</span>
</div>
<div class="abs logo"><div class="dot"></div><div><div class="wordmark">Lumavex</div><small>Precision you can rely on!</small></div></div>
<nav class="abs nav">
  <span class="active">ENDOSCOPE REPAIR</span><span>ENDOSCOPY SYSTEMS</span><span>ENDOSCOPY ACCESSORIES</span><span>ACCESSORIES CATALOG</span><span>PURCHASE</span>
</nav>

<!-- hero -->
<div class="abs hero"></div>
<div class="abs hero-photo" role="img" aria-label="Photo of two flexible endoscope control handles"></div>
<div class="abs hero-text">
  <p>WELCOME TO LUMAVEX</p>
  <h1>PUT YOUR ENDOSCOPE<br>IN RELIABLE HANDS!</h1>
</div>
<div class="btn btn-blue" style="left:104px;top:420px;width:165px;height:40px">Learn more</div>
<svg class="abs" style="left:0;top:560px" width="1200" height="160" viewBox="0 0 1200 160">
  <path d="M0 40 Q600 180 1200 30 L1200 160 L0 160Z" fill="#fff"/>
  <path d="M0 32 Q600 170 1200 22" fill="none" stroke="#2a9fe0" stroke-width="7"/>
</svg>
<svg class="abs" style="left:562px;top:652px" width="76" height="76" viewBox="0 0 76 76">
  <circle cx="38" cy="38" r="36" fill="#fff" stroke="#2a9fe0" stroke-width="2"/>
  <path d="M38 24v28M28 42l10 10 10-10" fill="none" stroke="#2a9fe0" stroke-width="2"/>
</svg>

<!-- service -->
<section class="abs service">
  <h2>YOUR FUTURE <span>OUR SERVICE</span></h2>
  <p>Lumavex GmbH is specialised in the repair and sale of Orvane, Pentira and Kaminon flexible medical endoscopes. As a service-oriented company, we are at your side with our knowledge and skills!</p>
</section>
<div class="abs" style="left:599px;top:1082px;width:2px;height:70px;background:var(--blue)"></div>

<!-- intro -->
<div class="abs intro-photo" role="img" aria-label="Close-up photo of an endoscope control head"></div>
<div class="abs intro">
  <h3>Endoscope repairs and second hand endoscopes from Lumavex cause the outcome matters!</h3>
  <p>Lumavex is a privileged partner for the start-up facility or optimisation of existing healthcare facilities, doctor's offices and hospitals. The quality and reliability of our products and our offered service are our best advertisement!</p>
  <p>As a result of optimised processes and highly qualified specialists in our company, we can work very quickly and with high quality for your benefit of least possible restrictions in your doctor's office or in your hospital.</p>
</div>
<div class="abs brands">
  <div style="background:#1a4f86">ORVANE</div><div style="background:var(--red)">PENTIRA</div><div style="background:#111">KAMINON</div>
</div>

<!-- cards -->
<div class="card" style="left:100px">
  <div class="icon"><svg width="40" height="40" viewBox="0 0 40 40" fill="none" stroke="#fff" stroke-width="2"><circle cx="14" cy="20" r="8"/><path d="M22 20h14M30 16v8"/></svg></div>
  <h4>Repair</h4><h5>Endoscope repair service</h5>
  <p>Manufacturer-independent we repair and maintain endoscopes, individual components</p>
  <div class="btn btn-blue" style="left:32px;top:213px;width:142px;height:38px;font-size:11px">Repair request</div>
</div>
<div class="card featured" style="left:440px">
  <div class="icon"><svg width="40" height="40" viewBox="0 0 40 40" fill="none" stroke="#fff" stroke-width="2"><circle cx="22" cy="22" r="9"/><path d="M10 8v14"/></svg></div>
  <h4>Sale</h4><h5>Used endoscopes</h5>
  <p>Our regular stock includes refurbished gastroscopes, coloscopes, bronchoscopes, cystoscopes and duodenoscopes from the well-known manufacturers Orvane, Pentira and Kaminon.</p>
  <div class="btn btn-navy" style="left:38px;top:224px;width:152px;height:38px;font-size:11px">Purchse request</div>
</div>
<div class="card" style="left:778px">
  <div class="icon"><svg width="40" height="40" viewBox="0 0 40 40" fill="none" stroke="#fff" stroke-width="2"><rect x="14" y="6" width="12" height="16" rx="3"/><path d="M20 22v12"/></svg></div>
  <h4>Purchase</h4><h5>Used endoscopes</h5>
  <p>We are very interested in buying your old endoscopes – even defective and dismantled! We offer fair conditions! Please contact us for a purchase offer!</p>
  <div class="btn btn-blue" style="left:32px;top:213px;width:138px;height:38px;font-size:11px">Sell device</div>
</div>

<!-- faulty -->
<div class="abs faulty"></div>
<div class="abs faulty-text">
  <h2>Faulty <span>Endoscope?</span></h2>
  <h3>We ensure quick and smooth repairs!</h3>
  <p>Lorem ipsum dolor sit amet, consectetur adipiscing elit, sed do eiusmod tempor incididunt ut labore et dolore magna aliqua. Ut enim ad minim veniam, quis nostrud exercitation ullamco laboris n</p>
</div>
<div class="btn btn-navy" style="left:130px;top:2492px;width:175px;height:46px;font-size:13px">Pick up order</div>
<div class="abs faulty-photo" role="img" aria-label="Photo of an endoscope handle on white"></div>

<!-- outcome -->
<h2 class="h-center" style="top:2735px;font-size:32px">Cause the <span style="color:var(--blue)">Outcome Matters</span></h2>
<div class="abs grid">
  <div class="cell hl"><svg class="ico" width="42" height="42" viewBox="0 0 42 42" fill="none" stroke="#fff" stroke-width="2"><circle cx="21" cy="21" r="14"/><circle cx="21" cy="21" r="5"/></svg><h4>One company for everyone</h4><p>We are a service provider for doctors and hospitals!</p></div>
  <div class="cell"><svg class="ico" width="50" height="50" viewBox="0 0 50 50" fill="none" stroke="#2a9fe0" stroke-width="2"><circle cx="25" cy="12" r="6"/><rect x="8" y="26" width="34" height="18" rx="3"/></svg><h4>Experience<br>characterises us</h4><p>Our team has many years of experience in the business field!</p></div>
  <div class="cell"><svg class="ico" width="50" height="60" viewBox="0 0 50 60" fill="none" stroke="#2a9fe0" stroke-width="2"><rect x="8" y="6" width="16" height="22" rx="3"/><path d="M16 28v24M24 12h14v14"/></svg><h4>The product is close<br>to our hearts</h4><p>We repair and sell second hand, flexible endoscopes!</p></div>
  <div class="cell"><svg class="ico" width="46" height="56" viewBox="0 0 46 56" fill="none" stroke="#2a9fe0" stroke-width="2"><path d="M23 4l18 7v14c0 13-9 22-18 26C14 47 5 38 5 25V11z"/><path d="M15 27l6 6 11-12"/></svg><h4>Guaranteed service</h4><p>You receive a six-month warranty on all repairs!</p></div>
  <div class="cell"><svg class="ico" width="60" height="54" viewBox="0 0 60 54" fill="none" stroke="#2a9fe0" stroke-width="2"><path d="M30 4l4 9 9 1-7 6 2 9-8-5-8 5 2-9-7-6 9-1z"/><path d="M4 44h16l14 4 20-10"/></svg><h4>Quality not quantity</h4><p>Reliability and durability instead of inferior replacements!</p></div>
  <div class="cell"><svg class="ico" width="50" height="60" viewBox="0 0 50 60" fill="none" stroke="#2a9fe0" stroke-width="2"><path d="M20 4l16 6v12c0 12-8 20-16 24C12 42 4 34 4 22V10z"/><circle cx="34" cy="40" r="8"/></svg><h4>Services for everyone</h4><p>Our service includes the manufacturers Orvane, Pentira and Kaminon!</p></div>
</div>

<!-- decision -->
<div class="abs decision"></div>
<h2 class="h-center" style="top:3455px;font-size:26px;line-height:1.25">LUMAVEX GMBH, YOUR DECISION<br>FOR YOUR FUTURE</h2>
<svg class="abs" style="left:395px;top:3540px" width="400" height="360" viewBox="0 0 400 360">
  <circle cx="200" cy="180" r="150" fill="none" stroke="#2a9fe0" stroke-width="1.5"/>
  <path d="M10 30h60M10 180h60M10 300h60M330 30h60M330 180h60M330 300h60" stroke="#2a9fe0" stroke-width="1.5"/>
</svg>
<div class="abs" style="left:475px;top:3600px;width:240px;height:240px;border-radius:50%;background:linear-gradient(135deg,#1a7fc6,#3ab3f0);border:6px solid #fff;box-shadow:0 0 0 2px #2a9fe0;display:flex;flex-direction:column;align-items:center;justify-content:center;color:#fff">
  <div style="font-size:26px;font-weight:700">Lumavex</div>
  <div style="font-size:10px">Precision you can rely on!</div>
</div>
<div class="feat l" style="left:100px;top:3568px"><h5>Fast Repairs</h5>Keep potential disruptions in your doctor's office or in your hospital at minimum</div>
<div class="feat l" style="left:100px;top:3685px"><h5>On-site service</h5>We will gladly pay you a visit to carry out analysis and repairs on site. Due to our many years of experience</div>
<div class="feat l" style="left:100px;top:3810px"><h5>Without a maintenance contract</h5>No subscription or other maintenance contract, but one-time and sustainable repair work</div>
<div class="feat" style="left:838px;top:3568px"><h5>Highly cost efficient</h5>Benefit from our first class recommendations and implementation by our experienced staff.</div>
<div class="feat" style="left:838px;top:3680px"><h5>Loan equipment service</h5>We will gladly pay you a visit to carry out analysis and repairs on site. Due to our many years of experience</div>
<div class="feat" style="left:838px;top:3815px"><h5>First class service</h5>Our clients always come first!</div>
<div class="fi b" style="left:372px;top:3542px"><svg width="26" height="26" fill="none" stroke="#fff" stroke-width="2"><path d="M4 22L22 4M4 4l18 18"/></svg></div>
<div class="fi n" style="left:365px;top:3688px"><svg width="26" height="26" fill="none" stroke="#fff" stroke-width="2"><circle cx="13" cy="13" r="8"/><circle cx="13" cy="13" r="3"/></svg></div>
<div class="fi b" style="left:372px;top:3802px"><svg width="26" height="26" fill="none" stroke="#fff" stroke-width="2"><rect x="4" y="6" width="18" height="14"/></svg></div>
<div class="fi n" style="left:762px;top:3542px"><svg width="26" height="26" fill="none" stroke="#fff" stroke-width="2"><circle cx="13" cy="10" r="6"/><path d="M4 24h18"/></svg></div>
<div class="fi b" style="left:770px;top:3688px"><svg width="26" height="26" fill="none" stroke="#fff" stroke-width="2"><rect x="5" y="5" width="16" height="16" rx="3"/></svg></div>
<div class="fi n" style="left:765px;top:3802px"><svg width="26" height="26" fill="none" stroke="#fff" stroke-width="2"><path d="M13 3l3 6 7 1-5 5 1 7-6-3-6 3 1-7-5-5 7-1z"/></svg></div>
<div class="btn btn-blue" style="left:475px;top:3898px;width:275px;height:46px;border-radius:12px 12px 0 12px;text-transform:none;font-size:14px">Learn more about Lumavex</div>

<!-- help form -->
<div class="abs help"></div>
<h2 class="h-center" style="top:4095px;font-size:30px;color:#fff">HOW CAN WE HELP YOU?</h2>
<div class="abs" style="left:557px;top:4142px;width:86px;height:2px;background:var(--blue)"></div>
<div class="field" style="left:227px;top:4172px;width:373px">👤 First name</div>
<div class="field" style="left:608px;top:4172px;width:374px">✆ Phone number</div>
<div class="field" style="left:227px;top:4227px;width:373px">👤 Last name</div>
<div class="field" style="left:608px;top:4227px;width:374px">✉ Email address</div>
<div class="field" style="left:227px;top:4282px;width:755px;height:92px;align-items:flex-start;padding-top:14px">Comments</div>
<div class="btn btn-blue" style="left:538px;top:4398px;width:145px;height:38px;font-size:14px">Submit</div>

<!-- footer -->
<footer class="abs footer"></footer>
<div class="abs" style="left:125px;top:4598px;color:#fff;display:flex;align-items:center;gap:10px">
  <div style="width:14px;height:14px;border-radius:50%;background:#fff"></div>
  <div>
    <div style="font-size:24px;font-weight:700">Lumavex</div>
    <div style="font-size:10px;font-weight:500">Precision you can rely on!</div>
  </div>
</div>
<p class="abs" style="left:123px;top:4686px;width:270px;font-size:12px;line-height:1.35;color:#cfe8f8">Lorem ipsum dolor sit amet, consectetur adipiscing elit, sed do eiusmod tempor incididunt ut labore et dolore</p>
<div class="fcol" style="left:487px;color:#fff"><h6>NAVIGATION</h6>Home<br>Endoscope Repair<br>Used Endoscope<br>Endoscopy Systems</div>
<div class="fcol" style="left:718px;color:#fff"><h6>RESOURCES</h6>Endoscopy Accesories<br>Purchase<br>Contact Us</div>
<div class="fcol" style="left:932px;color:#fff"><h6>FOLLOW US</h6></div>
<div class="abs" style="left:934px;top:4623px;display:flex;gap:7px">
  <div style="width:27px;height:27px;border-radius:50%;background:#fff"></div>
  <div style="width:27px;height:27px;border-radius:50%;background:#fff"></div>
  <div style="width:27px;height:27px;border-radius:50%;background:#fff"></div>
  <div style="width:27px;height:27px;border-radius:50%;background:#fff"></div>
</div>
<p class="abs" style="left:0;top:4830px;width:1200px;text-align:center;font-size:11px;color:#d8eefb">© 2022 Lumavex GmbH</p>

</body>
</html>
```